Networking Events Calendar/Diary

We need a responsive website that can act as both an online diary/calendar and a resource for community and networking events similar to brimtolvenquarrix.com (we do not want a clone, but one with similar functionality). We need to be able to host adverts, have a client area for clients to add their own events to the diary. This needs to have the functionality that clients have to pay to add recurring events. Some integration would be useful so that if a clients already has their own online diary on their website then using an API possibly to also add that event into our online diary

Industry/Entity Type

Events

Coding

Coded - Design and coding required

Number of Pages Required

5+ page

Requirements
Must have
• My project must have a calendar area, space for ads, be responsive and easily viewable on mobile. A subscribers area for clients and a way to purchase premium status so that premium events are highlighted.

```html
<!DOCTYPE html>
<html lang="en">
<head>
<meta charset="utf-8">
<title>Velmora Events</title>
<link href="https://fonts.googleapis.com/css2?family=Raleway:wght@400;500;600;700&family=Open+Sans:wght@400;600;700&display=swap" rel="stylesheet">
<style>
:root{
  --navy:#0d3c6e;
  --navy-dark:#082c52;
  --blue:#1a5a94;
  --link:#1d4f86;
  --orange:#f4a51c;
  --orange-deep:#ef7d12;
  --text:#555;
  --muted:#888;
  --line:#dcdcdc;
  --white:#fff;
}
*{box-sizing:border-box;margin:0;padding:0}
html,body{width:704px;height:1200px;overflow:hidden;background:var(--white)}
body{position:relative;font-family:"Open Sans",sans-serif;color:var(--text);font-size:6px}
.abs{position:absolute}
.site-header{left:0;top:0;width:704px;height:59px}
.brand{left:113px;top:18px;font-family:"Raleway",sans-serif;font-weight:500;font-size:21px;color:var(--navy);letter-spacing:.3px;white-space:nowrap}
.top-ad{left:290px;top:13px;width:298px;height:37px;border:1px solid #e2e2e2;display:flex}
.top-ad .pitch{width:122px;background:#e8b010;color:var(--white);padding:5px 7px;font-family:"Raleway",sans-serif}
.top-ad .pitch b{display:block;font-size:8.5px;font-weight:600}
.top-ad .pitch small{font-size:5px;opacity:.85}
.top-ad .shot{width:48px;background:linear-gradient(#3a3a3a,#6d6d6d)}
.top-ad .vendor{flex:1;display:flex;align-items:center;justify-content:space-around;font-size:7.5px;font-weight:700;color:#333}
.top-ad .vendor span{background:#5aaa45;color:var(--white);font-size:5px;font-weight:400;padding:3px 5px}
.main-nav{left:0;top:59px;width:704px;height:26px;background:var(--navy);display:flex;padding-left:112px}
.main-nav a{font-family:"Raleway",sans-serif;font-weight:500;font-size:8px;color:var(--white);text-decoration:none;padding:0 13px;line-height:26px;border-right:1px solid rgba(255,255,255,.12)}
.main-nav a.active{background:var(--navy-dark)}
.hero{left:0;top:85px;width:704px;height:238px;background:linear-gradient(90deg,#5b3e22 0%,#3a3b40 35%,#2c3340 60%,#6a5236 100%)}
.hero-copy{left:115px;top:142px;width:320px;font-family:"Raleway",sans-serif}
.hero-copy .kicker{color:var(--orange);font-size:13.5px;font-weight:600;white-space:nowrap}
.hero-copy h1{color:var(--white);font-size:22px;font-weight:600;margin-top:2px;white-space:nowrap}
.hero-copy p{color:var(--white);font-size:6px;margin-top:7px;line-height:1.7;font-family:"Open Sans",sans-serif}
.dots{display:flex;gap:3px;margin-top:5px}
.dots i{width:9px;height:9px;border-radius:50%;background:var(--white);display:block}
.dots i.on{background:var(--orange);border:1px solid var(--white)}
.section-title{font-family:"Raleway",sans-serif;font-size:13px;font-weight:500;color:#222;padding-bottom:3px;border-bottom:2px solid var(--navy);display:inline-block}
.section-title.alt{color:var(--orange);border-color:var(--orange)}
.events{left:112px;top:343px;width:335px}
.event{display:flex;gap:8px;margin-top:13px;height:57px}
.event:first-of-type{margin-top:14px}
.thumb{width:86px;height:57px;flex:none}
.event h3{font-family:"Raleway",sans-serif;font-weight:500;font-size:8.5px;color:var(--link)}
.event p{font-size:5.5px;line-height:1.6;margin-top:4px;padding-left:2px}
.event time{display:block;font-size:5.6px;margin-top:5px}
.calendar{left:473px;top:341px;width:119px}
.cal-head{background:var(--navy);color:var(--white);font-family:"Raleway",sans-serif;font-size:7.5px;font-weight:500;height:15px;display:flex;justify-content:space-between;align-items:center;padding:0 6px;border-radius:3px 3px 0 0}
.calendar table{width:100%;border-collapse:collapse;font-size:6px;text-align:center}
.calendar th{background:var(--orange);color:var(--white);font-weight:400;font-size:5px;height:8px}
.calendar td{border:1px solid #e3e3e3;height:13.5px;color:#333}
.calendar td.out{color:#aaa}
.calendar td.today{background:#222;color:var(--white)}
.cta{left:466px;width:127px;height:24px;border-radius:12px 0 0 12px;display:flex;align-items:center;color:var(--white);font-family:"Raleway",sans-serif;font-size:8.5px}
.cta .ico{width:24px;height:24px;border-radius:50%;border:2px solid var(--white);display:flex;align-items:center;justify-content:center;margin-right:7px}
.cta .chev{margin-left:auto;margin-right:5px}
.cta.register{top:462px;background:var(--blue)}
.cta.register .ico{background:var(--navy)}
.cta.subscribe{top:491px;background:var(--orange)}
.cta.subscribe .ico{background:var(--orange-deep)}
.sponsor{left:469px;top:529px;width:124px;height:103px;border:1px solid #c9a24b;background:linear-gradient(#f7e7b8,#e6b960);font-family:"Raleway",sans-serif}
.sponsor .mark{left:9px;top:8px;width:12px;height:12px;border-radius:50%;background:#222}
.sponsor .name{left:0;width:100%;top:40px;text-align:center;font-size:18px;color:#b9582c;font-weight:500}
.sponsor .tag{left:0;width:100%;top:63px;text-align:center;font-size:9px;color:#b9582c}
.sponsor .foot{left:0;bottom:0;width:100%;height:16px;background:#6b3a1c;color:#e8c58a;font-size:5.5px;display:flex;align-items:center;justify-content:flex-end;padding-right:4px;gap:4px}
.sponsor .foot b{background:#4a2a6a;color:var(--white);font-size:7px;padding:1px 3px}
.blog{left:112px;top:675px;width:482px}
.carousel{left:558px;top:682px;display:flex;gap:4px}
.carousel i{width:12px;height:12px;border-radius:50%;background:#e5e5e5;display:flex;align-items:center;justify-content:center;font-style:normal;font-size:8px;color:#555}
.posts{display:flex;gap:13px;margin-top:12px}
.post{width:152px}
.post .thumb{width:152px;height:68px}
.post h3{font-family:"Raleway",sans-serif;font-weight:500;font-size:8px;color:var(--link);margin-top:10px;padding-left:2px}
.post p{font-size:5.5px;line-height:1.65;margin-top:5px;padding-left:2px}
.post a{display:block;font-size:6px;color:#444;margin-top:6px;text-decoration:none;padding-left:2px}
.news{left:110px;top:862px;width:484px}
.cards{display:flex;gap:6px;margin-top:12px}
.card{width:117px;height:129px;border:1px solid #e0e0e0;text-align:center}
.card .banner{height:63px;color:var(--white);padding-top:15px;font-family:"Raleway",sans-serif}
.card.blue .banner{background:linear-gradient(135deg,#2c6aa3,#0f4478)}
.card.orange .banner{background:linear-gradient(135deg,#f6a62a,#e9670f)}
.card .banner span{font-size:7.5px;display:block}
.card .banner b{font-size:7.5px;font-weight:700;display:block;margin-top:3px}
.card .banner small{font-size:5.5px;font-weight:700;display:block;margin-top:2px}
.card p{font-size:5.5px;line-height:1.9;padding:11px 7px 0}
.card a{display:block;font-size:5.5px;font-weight:700;color:var(--link);text-decoration:none;margin-top:5px}
.site-footer{left:0;top:1045px;width:704px;height:130px;background:linear-gradient(#0f5289,#0c3e70)}
.foot-col{top:1069px;color:var(--white)}
.foot-col h4{font-family:"Raleway",sans-serif;font-weight:400;font-size:10.5px}
.foot-col ul{list-style:none;margin-top:4px}
.foot-col li{font-size:6px;line-height:13px}
.foot-col p{font-size:6px;margin-top:6px}
.signup input{display:block;width:126px;height:15px;margin-top:6px;border:none;background:#eef0f2;font-size:5px;padding-left:16px;font-family:"Open Sans",sans-serif}
.signup button{margin-top:6px;background:var(--orange);border:none;color:var(--white);font-family:"Raleway",sans-serif;font-size:8px;padding:4px 9px}
.social{display:flex;gap:3px;margin-top:6px}
.social i{width:17px;height:17px;border-radius:50%;border:1.5px solid var(--white);display:block}
.legal{left:0;top:1175px;width:704px;height:25px;background:var(--blue);color:#b8cde2;font-size:5.5px;padding:13px 0 0 112px}
</style>
</head>
<body>
<header class="site-header abs">
  <div class="brand abs">Velmora Events</div>
  <aside class="top-ad abs" aria-label="Advertisement">
    <div class="pitch"><b>Create your online store</b><small>It only takes 60 seconds</small></div>
    <div class="shot" role="img" aria-label="Online store preview screenshot"></div>
    <div class="vendor">Storevane <span>Get started for free</span></div>
  </aside>
</header>

<nav class="main-nav abs">
  <a class="active" href="#">HOME</a><a href="#">LATEST NEWS</a><a href="#">UPCOMING EVENT</a><a href="#">OUR DIARY</a><a href="#">CALENDAR</a><a href="#">BLOG</a><a href="#">CONTACT</a>
</nav>

<section class="hero abs" role="img" aria-label="Business people networking with drinks at an event"></section>
<div class="hero-copy abs">
  <div class="kicker">WELCOME TO VELMORA EVENTS</div>
  <h1>PELLENTESQUE RUTRUM</h1>
  <p>eleifend quam leo molestie sed luctus quis feugiat in pede Fusce tellus Sed<br>metus augue Vivamus porttitor purus nisi eleifend libero</p>
  <div class="dots"><i class="on"></i><i></i><i></i><i></i></div>
</div>

<section class="events abs">
  <h2 class="section-title">UPCOMING EVENTS</h2>
  <article class="event"><div class="thumb" role="img" aria-label="Audience applauding at a seminar" style="background:linear-gradient(135deg,#a9b8c6,#4b6076)"></div>
    <div><h3>Etiam Sed porta Suspendisse</h3><p>Ut nisi erat fermentum vel congue id euismod in elit Fusce ultricies orci ac feugiat suscipit leo massa sodales velit et scelerisque mi tortor at ipsum cligula augue bibendum accumsan vestibulum ut commodo a mi Morbi ornare</p><time>Wednesday, 11 Nov 2015</time></div></article>
  <article class="event"><div class="thumb" role="img" aria-label="Banquet hall with purple lighting" style="background:linear-gradient(135deg,#8a4fa0,#e0b9c9)"></div>
    <div><h3>Duis quam Nam eget lacus Aliquam erat</h3><p>Ut nisi erat fermentum vel congue id euismod in elit Fusce ultricies orci ac feugiat suscipit leo massa sodales velit et scelerisque mi tortor at ipsum cligula augue bibendum accumsan vestibulum ut commodo a mi Morbi ornare</p><time>Wednesday, 11 Nov 2015</time></div></article>
  <article class="event"><div class="thumb" role="img" aria-label="Crowded exhibition hall at night" style="background:linear-gradient(135deg,#2a2a3a,#c49a4a)"></div>
    <div><h3>Morbi porta libero ullamcorper</h3><p>Ut nisi erat fermentum vel congue id euismod in elit Fusce ultricies orci ac feugiat suscipit leo massa sodales velit et scelerisque mi tortor at ipsum cligula augue bibendum accumsan vestibulum ut commodo a mi Morbi ornare</p><time>Wednesday, 11 Nov 2015</time></div></article>
  <article class="event"><div class="thumb" role="img" aria-label="Team meeting around a table" style="background:linear-gradient(135deg,#d8dde2,#7b8da0)"></div>
    <div><h3>Curabitur vel mi sit amet</h3><p>Ut nisi erat fermentum vel congue id euismod in elit Fusce ultricies orci ac feugiat suscipit leo massa sodales velit et scelerisque mi tortor at ipsum cligula augue bibendum accumsan vestibulum ut commodo a mi Morbi ornare</p><time>Wednesday, 11 Nov 2015</time></div></article>
</section>

<aside class="calendar abs">
  <div class="cal-head"><span>‹</span><span>DECEMBER</span><span>›</span></div>
  <table>
    <tr><th>Su</th><th>Mo</th><th>Tu</th><th>We</th><th>Th</th><th>Fr</th><th>Sa</th></tr>
    <tr><td class="out">28</td><td class="out">29</td><td class="out">30</td><td class="out">31</td><td>1</td><td>2</td><td>3</td></tr>
    <tr><td>4</td><td>5</td><td>6</td><td>7</td><td>8</td><td>9</td><td>10</td></tr>
    <tr><td>11</td><td>12</td><td>13</td><td>14</td><td>15</td><td>16</td><td>17</td></tr>
    <tr><td>18</td><td>19</td><td class="today">20</td><td>21</td><td>22</td><td>23</td><td>24</td></tr>
    <tr><td>25</td><td>26</td><td>27</td><td>28</td><td>29</td><td>30</td><td class="out">1</td></tr>
    <tr><td class="out">2</td><td class="out">3</td><td class="out">4</td><td class="out">5</td><td class="out">6</td><td class="out">7</td><td class="out">8</td></tr>
  </table>
</aside>

<a class="cta register abs"><span class="ico"><svg width="10" height="10" viewBox="0 0 10 10"><rect x="1" y="2" width="6" height="7" fill="none" stroke="#fff"/><path d="M4 6 L9 1" stroke="#fff" stroke-width="1.2"/></svg></span>Register with Us<span class="chev">›</span></a>
<a class="cta subscribe abs"><span class="ico"><svg width="10" height="8" viewBox="0 0 10 8"><rect x=".5" y=".5" width="9" height="7" fill="#fff"/><path d="M.5 .5 L5 4.5 L9.5 .5" fill="none" stroke="#ef7d12"/></svg></span>Subscribe Now<span class="chev">›</span></a>

<aside class="sponsor abs" aria-label="Sponsor advertisement">
  <i class="mark abs"></i>
  <div class="abs" style="left:7px;top:22px;font-size:5px;font-weight:700;color:#222">Hearthway</div>
  <div class="name abs">Kindred Den</div>
  <div class="tag abs">New Beginnings</div>
  <div class="foot abs">proudly sponsored by <b>Brindle</b></div>
</aside>

<section class="blog abs">
  <h2 class="section-title alt">LATEST BLOG POSTS</h2>
  <div class="posts">
    <article class="post"><div class="thumb" role="img" aria-label="Empty conference hall with rows of chairs" style="background:linear-gradient(135deg,#7a5230,#c08a50)"></div><h3>Etiam Sed porta Suspendisse</h3><p>leo molestie sed luctus quis feugiat in pede Fusce tellus Sed metus augue convallis et vehicula ut pulvinar eu ante Integer</p><a href="#">READ MORE</a></article>
    <article class="post"><div class="thumb" role="img" aria-label="Audience clapping at a business event" style="background:linear-gradient(135deg,#dcdcdc,#3c3f48)"></div><h3>Nostra per inceptos hymena</h3><p>leo molestie sed luctus quis feugiat in pede Fusce tellus Sed metus augue convallis et vehicula ut pulvinar eu ante Integer</p><a href="#">READ MORE</a></article>
    <article class="post"><div class="thumb" role="img" aria-label="Outdoor banquet tables set for dinner" style="background:linear-gradient(135deg,#6b7a4a,#d8dde0)"></div><h3>Etiam Sed porta Suspendisse</h3><p>leo molestie sed luctus quis feugiat in pede Fusce tellus Sed metus augue convallis et vehicula ut pulvinar eu ante Integer</p><a href="#">READ MORE</a></article>
  </div>
</section>
<div class="carousel abs"><i>‹</i><i>›</i></div>

<section class="news abs">
  <h2 class="section-title">RECENT NEWS</h2>
  <div class="cards">
    <article class="card blue"><div class="banner"><span>02 NOV 2015</span><b>CUM SOCIS NATOQUE</b><small>PENATIBUS MAGNIS</small></div><p>Ut nisi erat fermentum vel congue id euismod in elit Fusce ultricies orci ac feugiat suscipit leo massa</p><a href="#">READ MORE</a></article>
    <article class="card orange"><div class="banner"><span>05 NOV 2015</span><b>CUM SOCIS NATOQUE</b><small>PENATIBUS MAGNIS</small></div><p>Ut nisi erat fermentum vel congue id euismod in elit Fusce ultricies orci ac feugiat suscipit leo massa</p><a href="#">READ MORE</a></article>
    <article class="card blue"><div class="banner"><span>15 NOV 2015</span><b>CUM SOCIS NATOQUE</b><small>PENATIBUS MAGNIS</small></div><p>Ut nisi erat fermentum vel congue id euismod in elit Fusce ultricies orci ac feugiat suscipit leo massa</p><a href="#">READ MORE</a></article>
    <article class="card orange"><div class="banner"><span>20 NOV 2015</span><b>CUM SOCIS NATOQUE</b><small>PENATIBUS MAGNIS</small></div><p>Ut nisi erat fermentum vel congue id euismod in elit Fusce ultricies orci ac feugiat suscipit leo massa</p><a href="#">READ MORE</a></article>
  </div>
</section>

<footer class="site-footer abs"></footer>
<div class="foot-col abs" style="left:111px"><h4>Quick links</h4><ul><li>About Us</li><li>What We Do</li><li>How we work</li><li>Blog Post</li><li>News &amp; Events</li></ul></div>
<div class="foot-col abs" style="left:219px"><h4>Resources</h4><ul><li>Mauris vel lacus</li><li>Vitae felis vestibulum</li><li>Aolutpat imperdiet</li><li>Cum sociis</li><li>Natoque penatibus</li></ul></div>
<div class="foot-col signup abs" style="left:329px"><h4>Newsletters Sign Up</h4><p>Plesae sign up here for latest news</p><input type="text" placeholder="Email address"><button>Subscribe</button></div>
<div class="foot-col abs" style="left:503px"><h4>Stay in touch</h4><div class="social"><i></i><i></i><i></i></div></div>
<div class="legal abs">© 2015 Company Name&nbsp; All right reserved&nbsp; Term of Use</div>
</body>
</html>
```